Modern Medical Optometry Website

We need mordern, Patient friendly website. Easy to navigate and enhance our advance medical technology and excellent patient care.
1. HOME PAGE
2. OUR TEAM PAGE
3. EYECARE PAGE - VISION SERVICES, EYE EXAMS, KERATOCONUS CENTER, GLAUCOMA , DIABITES, MELORIDEX EXAM, DIGITAL RETINAL, OCT.
4. MYOPIA CONTROL CLINIC
5. DRY EYE CLINIC
6. EYEWEAR
7. PATIENT CENTER - BLOG
7. CONTACT US
This is our current website www.brivaloka.com
and We want to add more content and a cleaner design like these website
http://tarnwickfolvendale.com/
https://www.qmvorlu.com/

```html
<!DOCTYPE html>
<html lang="en">
<head>
<meta charset="utf-8">
<title>Lumora Optometry</title>
<link rel="stylesheet" href="https://fonts.googleapis.com/css2?family=Questrial&family=Mulish:wght@400;600;700;800&display=swap">
<style>
:root{
  --teal:#1a8fae;
  --teal-dark:#137893;
  --teal-deep:#0f6a83;
  --yellow:#f8d81a;
  --ink:#2b2b2b;
  --grey-text:#555;
  --light:#efefef;
  --footer:#1e1e1e;
  --footer-bottom:#141414;
  --white:#fff;
}
*{box-sizing:border-box;margin:0;padding:0}
html,body{width:1200px;height:3673px;overflow:hidden}
body{position:relative;font-family:'Mulish',sans-serif;color:var(--ink);background:var(--white)}
.abs{position:absolute}
.heading{font-family:'Questrial',sans-serif;letter-spacing:3px;text-transform:uppercase;font-weight:400}

/* header */
.site-header{position:absolute;left:0;top:0;width:1200px;height:135px;background:var(--white)}
.topbar{position:absolute;left:560px;top:0;width:640px;height:36px;background:var(--yellow)}
.call-line{position:absolute;left:582px;top:0;height:36px;display:flex;align-items:center;gap:10px;font-weight:700;font-size:16px;white-space:nowrap}
.call-line .phone-dot{width:30px;height:30px;border-radius:50%;background:var(--teal);display:flex;align-items:center;justify-content:center}
.appt-top{position:absolute;left:875px;top:0;width:247px;height:54px;background:var(--teal);color:var(--white);font-family:'Questrial',sans-serif;font-size:17px;letter-spacing:1px;display:flex;align-items:center;justify-content:center;white-space:nowrap}
.brand{position:absolute;left:70px;top:18px;display:flex;align-items:center;gap:10px}
.brand .mark{width:22px;height:22px;background:var(--yellow)}
.brand .name{font-weight:800;font-size:22px;color:var(--ink);letter-spacing:1px}
.main-nav{position:absolute;left:272px;top:90px;display:flex;gap:28px;font-size:14px;font-weight:600;color:#333;white-space:nowrap}
.main-nav a{color:inherit;text-decoration:none;position:relative}
.main-nav a.active{color:var(--teal);font-weight:800}
.main-nav a.active::after{content:"";position:absolute;left:50%;top:28px;margin-left:-14px;border-left:14px solid transparent;border-right:14px solid transparent;border-bottom:14px solid var(--teal)}

/* hero */
.hero{position:absolute;left:0;top:135px;width:1200px;height:543px;background:linear-gradient(100deg,#6f5a4d 0%,#a48d7e 35%,#d8c4b3 60%,#8d6a56 85%,#5e4537 100%)}
.hero-title{position:absolute;left:80px;top:148px;font-weight:800;font-size:42px;color:var(--white);letter-spacing:1px}
.hero-text{position:absolute;left:80px;top:208px;width:440px;font-size:15px;line-height:26px;color:var(--white);font-weight:600}
.hero-phone{position:absolute;left:76px;top:264px;font-size:32px;font-weight:800;color:var(--yellow)}
.hero-phone span{font-size:24px}
.hero-btn{position:absolute;left:76px;top:328px;width:272px;height:52px;background:var(--teal);color:var(--white);font-family:'Questrial',sans-serif;font-size:17px;letter-spacing:1px;display:flex;align-items:center;justify-content:center}
.slider-arrow{position:absolute;top:248px;width:50px;height:50px;border-radius:50%;background:rgba(0,0,0,.45);display:flex;align-items:center;justify-content:center}

/* promise */
.promise{position:absolute;left:0;top:678px;width:1200px;height:505px;background:var(--white)}
.promise-visual{position:absolute;left:0;top:0;width:600px;height:505px;background:radial-gradient(circle at 300px 260px,#3e7bb6 0,#6c9ccc 45px,#505a62 95px,#b7bcc0 170px,#e9eaeb 290px,#fafafa 420px)}
.promise-title{position:absolute;left:612px;top:70px;font-size:38px;color:#222}
.promise-copy{position:absolute;left:622px;top:124px;width:490px;font-size:14px;line-height:26px;color:var(--grey-text)}
.promise-copy p+p{margin-top:18px}
.learn-btn{position:absolute;left:624px;top:392px;width:168px;height:52px;background:var(--yellow);font-family:'Questrial',sans-serif;font-size:16px;letter-spacing:1px;display:flex;align-items:center;justify-content:center;color:#222}

/* info band */
.info-band{position:absolute;left:0;top:1183px;width:1200px;height:347px}
.info-half{position:absolute;top:0;width:600px;height:347px;color:var(--white)}
.info-half.contact{left:0;background:var(--teal)}
.info-half.hours{left:600px;background:var(--teal-dark)}
.info-title{position:absolute;top:50px;width:600px;text-align:center;font-size:26px}
.info-list{position:absolute;list-style:none;font-size:16px;line-height:20px}
.info-list li{display:flex;align-items:flex-start;gap:18px;margin-bottom:17px}
.info-list svg{flex:none}
.lunch-note{position:absolute;left:0;top:262px;width:600px;text-align:center;font-size:16px}

/* tiles */
.tiles{position:absolute;left:0;top:1530px;width:1200px;height:539px;display:grid;grid-template-columns:repeat(4,300px);grid-template-rows:repeat(2,269.5px)}
.tile{position:relative;display:flex;align-items:center;justify-content:center;color:var(--white);font-weight:700;font-size:18px;letter-spacing:1px}
.tile--team{background:linear-gradient(160deg,#f8d81a,#d9b91a 60%,#a58d1c);font-family:'Questrial',sans-serif;font-size:30px;color:#222;padding-top:70px}
.tile--dry{background:linear-gradient(160deg,#4e3a25,#6f5839 50%,#3b2c1d)}
.tile--social{background:linear-gradient(160deg,#8a7c82,#c4aab4 55%,#6b6068)}
.tile--insurance{background:linear-gradient(160deg,#7d6d60,#a9978a 50%,#5c5048)}
.tile--exam{background:linear-gradient(160deg,#4b4f55,#6c7078 50%,#34373c)}
.tile--services{background:linear-gradient(160deg,#2f4a4f,#4a6468 50%,#233538)}
.tile--eyewear{background:linear-gradient(160deg,#a9652a,#d58b3c 50%,#7f4a1f)}
.tile--myopia{background:linear-gradient(160deg,#4c5563,#6f7889 50%,#373e48)}

/* testimonials */
.testimonials{position:absolute;left:0;top:2069px;width:1200px;height:336px;background:var(--yellow)}
.testimonial-photo{position:absolute;left:139px;top:45px;width:246px;height:246px;border-radius:50%;border:10px solid var(--teal);background:radial-gradient(circle at 50% 45%,#d9ccc2,#a6b4bf 70%,#8896a2)}
.testimonial-title{position:absolute;left:453px;top:84px;font-size:34px;color:#222}
.testimonial-quote{position:absolute;left:458px;top:140px;width:645px;font-size:15px;line-height:27px;font-style:italic;font-weight:600;color:var(--teal-deep)}
.testimonial-quote .q{font-family:'Questrial',sans-serif;font-style:normal;font-size:30px;color:var(--teal);vertical-align:-6px}
.client-name{position:absolute;left:960px;top:236px;font-family:'Questrial',sans-serif;font-size:16px;color:var(--teal-deep);letter-spacing:1px}
.client-name::before{content:"";display:inline-block;width:24px;height:2px;background:var(--teal-deep);vertical-align:middle;margin-right:8px}
.chev{position:absolute;top:160px}

/* partners */
.partners{position:absolute;left:0;top:2405px;width:1200px;height:296px;background:var(--light)}
.partners-title{position:absolute;left:0;top:62px;width:1200px;text-align:center;font-size:36px;color:#222}
.partner-row{position:absolute;left:148px;top:160px;width:920px;display:flex;justify-content:space-between;align-items:center}
.partner-badge{width:140px;height:58px;border-radius:4px;background:#cfcfcf}

/* eyewear section */
.eyewear-section{position:absolute;left:0;top:2701px;width:1200px;height:439px;background:var(--teal)}
.eyewear-title{position:absolute;left:0;top:68px;width:1200px;text-align:center;font-size:34px;color:var(--white)}
.product{position:absolute;top:158px;width:306px;text-align:center;color:var(--white)}
.product-visual{position:relative;margin:0 auto;width:306px;height:160px;border-radius:6px;background:radial-gradient(ellipse at 50% 55%,#3a3a3a 0,#1d1d1d 38%,rgba(22,80,99,0) 62%)}
.cart{position:absolute;right:2px;top:2px;width:38px;height:38px;border-radius:50%;background:var(--yellow);display:flex;align-items:center;justify-content:center}
.product-name{margin-top:14px;font-size:18px;font-weight:600;letter-spacing:.5px}
.product-price{margin-top:6px;font-size:20px;font-weight:800;color:var(--yellow)}

/* footer */
.site-footer{position:absolute;left:0;top:3140px;width:1200px;height:472px;background:var(--footer);color:#ddd}
.footer-brand{position:absolute;left:100px;top:70px;width:230px;text-align:center}
.footer-brand .mark{width:26px;height:26px;background:var(--yellow);margin:0 auto 12px}
.footer-brand .name{font-weight:800;font-size:26px;color:var(--yellow);letter-spacing:1px}
.cards-note{position:absolute;left:100px;top:192px;width:230px;text-align:center;font-size:14px;font-weight:700;color:var(--yellow)}
.social-row{position:absolute;left:134px;top:236px;display:flex;gap:14px}
.social-row span{width:40px;height:40px;border-radius:50%;background:#2f5ea8}
.social-row span:nth-child(2){background:#2f8fa8}
.social-row span:nth-child(3){background:#c0282d}
.footer-col{position:absolute;top:40px}
.footer-col h3{font-family:'Questrial',sans-serif;font-weight:400;font-size:18px;letter-spacing:1.5px;color:var(--teal);text-transform:uppercase;margin-bottom:24px;white-space:nowrap}
.footer-col ul{list-style:none;font-size:14px;line-height:22px}
.footer-col li{display:flex;gap:16px;align-items:flex-start;margin-bottom:14px}
.footer-col .dir{color:var(--yellow);font-size:13px;text-decoration:underline}
.newsletter p{width:250px;font-size:14px;line-height:26px;color:#ddd}
.news-input{margin-top:18px;width:248px;height:42px;background:#f0f0f0;color:#777;font-size:13px;padding:0 12px;display:flex;align-items:center}
.news-btn{margin-top:16px;width:142px;height:46px;background:var(--yellow);color:#222;font-family:'Questrial',sans-serif;font-size:15px;letter-spacing:1px;display:flex;align-items:center;justify-content:center}
.footer-badges{position:absolute;left:429px;top:362px;display:flex;gap:40px;align-items:center}
.footer-badges .b1{width:116px;height:72px;background:#f5f5f5;border-radius:3px}
.footer-badges .b2{width:196px;height:72px;background:#3a3a3a;border-radius:3px}
.copyright{position:absolute;left:0;top:3612px;width:1200px;height:61px;background:var(--footer-bottom);color:#bbb;font-size:14px;display:flex;align-items:center;justify-content:center}
.copyright b{color:var(--teal);font-weight:600;margin:0 4px}
</style>
</head>
<body>

<header class="site-header">
  <div class="topbar"></div>
  <div class="call-line">
    <span>Call Us On :</span>
    <span class="phone-dot"><svg width="16" height="16" viewBox="0 0 24 24"><path fill="#fff" d="M6.6 10.8a15.1 15.1 0 0 0 6.6 6.6l2.2-2.2a1 1 0 0 1 1-.25 11.4 11.4 0 0 0 3.6.57 1 1 0 0 1 1 1V20a1 1 0 0 1-1 1A17 17 0 0 1 3 4a1 1 0 0 1 1-1h3.5a1 1 0 0 1 1 1c0 1.250.2 2.45.57 3.6a1 1 0 0 1-.25 1z"/></svg></span>
    <span>555-204-7310</span>
  </div>
  <div class="appt-top">MAKE AN APPOINTMENT</div>
  <div class="brand"><span class="mark"></span><span class="name">LUMORA</span></div>
  <nav class="main-nav">
    <a class="active" href="#">HOME</a><a href="#">OUR TEAM</a><a href="#">EYECARE</a><a href="#">MYOPIA CONTROL CLINIC</a><a href="#">DRY EYE CLINIC</a><a href="#">EYEWEAR</a><a href="#">BLOG</a><a href="#">CONTACT US</a>
  </nav>
</header>

<section class="hero" role="img" aria-label="Smiling mother and daughter both wearing glasses">
  <h1 class="hero-title">LUMORA OPTOMETRY</h1>
  <p class="hero-text">Lorem Ipsum is simply dummy text of the printing and typesetting industry. Lorem Ipsum has been.</p>
  <div class="hero-phone">555-204-7310 / <span>Call Or Text Us</span></div>
  <div class="hero-btn">MAKE AN APPOINTMENT</div>
  <div class="slider-arrow" style="left:14px"><svg width="14" height="20" viewBox="0 0 14 20"><path d="M11 2 3 10l8 8" fill="none" stroke="#fff" stroke-width="3"/></svg></div>
  <div class="slider-arrow" style="left:1136px"><svg width="14" height="20" viewBox="0 0 14 20"><path d="m3 2 8 8-8 8" fill="none" stroke="#fff" stroke-width="3"/></svg></div>
</section>

<section class="promise">
  <div class="promise-visual" role="img" aria-label="Close-up of a blue eye"></div>
  <h2 class="promise-title heading">The Lumora Promise</h2>
  <div class="promise-copy">
    <p>Welcome to Lumora Optometry, where your vision and eye health are our sole priority. We take great pride in providing you with state-of-the-art eyecare matched with personal attention from our staff and doctors. Your quality of life is our goal and we believe that healthy eyesight is vital to achieving it.</p>
    <p>Our professional and personable staff is highly trained in helping you achieve and maintain healthy eyesight. Our optometrists have combined experiences and specialize in Orthokeratology (OrthoK), Ocular disease, Glaucoma diagnosis &amp; management.</p>
  </div>
  <div class="learn-btn">LEARN MORE</div>
</section>

<section class="info-band">
  <div class="info-half contact">
    <h3 class="info-title heading">Lumora Optometry</h3>
    <ul class="info-list" style="left:176px;top:114px">
      <li><svg width="18" height="22" viewBox="0 0 18 22"><path fill="#f8d81a" d="M9 0a8 8 0 0 0-8 8c0 6 8 14 8 14s8-8 8-14a8 8 0 0 0-8-8zm0 11a3 3 0 1 1 0-6 3 3 0 0 1 0 6z"/></svg><span>4820 Alderline Ave.,<br>Brookvale, CA 90120</span></li>
      <li><svg width="18" height="18" viewBox="0 0 24 24"><path fill="#f8d81a" d="M6.6 10.8a15.1 15.1 0 0 0 6.6 6.6l2.2-2.2a1 1 0 0 1 1-.25 11.4 11.4 0 0 0 3.6.57 1 1 0 0 1 1 1V20a1 1 0 0 1-1 1A17 17 0 0 1 3 4a1 1 0 0 1 1-1h3.5a1 1 0 0 1 1 1c0 1.25.2 2.45.57 3.6a1 1 0 0 1-.25 1z"/></svg><span>555-204-7310</span></li>
      <li><svg width="18" height="18" viewBox="0 0 18 18"><rect x="4" y="1" width="10" height="5" fill="#f8d81a"/><rect x="1" y="7" width="16" height="8" rx="1" fill="#f8d81a"/><rect x="4" y="12" width="10" height="5" fill="#f8d81a"/></svg><span>555-204-7370</span></li>
      <li><svg width="18" height="14" viewBox="0 0 18 14"><rect width="18" height="14" rx="1" fill="#f8d81a"/><path d="m1 1 8 7 8-7" fill="none" stroke="#1a8fae" stroke-width="1.6"/></svg><span>info@brivaloka.com</span></li>
    </ul>
  </div>
  <div class="info-half hours">
    <h3 class="info-title heading">Lumora Optometry</h3>
    <ul class="info-list" style="left:152px;top:114px">
      <li><svg width="18" height="18" viewBox="0 0 18 18"><circle cx="9" cy="9" r="8" fill="none" stroke="#f8d81a" stroke-width="2"/><path d="m5 9 3 3 5-6" fill="none" stroke="#f8d81a" stroke-width="2"/></svg><span>Monday - Thursday: 9 am - 6 pm</span></li>
      <li><svg width="18" height="18" viewBox="0 0 18 18"><circle cx="9" cy="9" r="8" fill="none" stroke="#f8d81a" stroke-width="2"/><path d="m5 9 3 3 5-6" fill="none" stroke="#f8d81a" stroke-width="2"/></svg><span>Friday: 8.30 am - 5 pm</span></li>
      <li><svg width="18" height="18" viewBox="0 0 18 18"><circle cx="9" cy="9" r="8" fill="none" stroke="#f8d81a" stroke-width="2"/><path d="m5 9 3 3 5-6" fill="none" stroke="#f8d81a" stroke-width="2"/></svg><span>Saturday: 8.30 am- 5 pm</span></li>
      <li><svg width="18" height="18" viewBox="0 0 18 18"><circle cx="9" cy="9" r="8" fill="none" stroke="#f8d81a" stroke-width="2"/><path d="m5 9 3 3 5-6" fill="none" stroke="#f8d81a" stroke-width="2"/></svg><span>Closed on Sundays</span></li>
    </ul>
    <p class="lunch-note">Please keep in mind we are closed for lunch 1-2 pm</p>
  </div>
</section>

<section class="tiles">
  <div class="tile tile--team" role="img" aria-label="Clinic team group photo"><span>TEAM</span></div>
  <div class="tile tile--dry" role="img" aria-label="Close-up of a dry eye"><span>DRY EYES</span></div>
  <div class="tile tile--social" role="img" aria-label="Friends posing with shopping bags"><span>SOCIAL</span></div>
  <div class="tile tile--insurance" role="img" aria-label="Smiling woman"><span>INSURANCE</span></div>
  <div class="tile tile--exam" role="img" aria-label="Patient at an eye exam phoropter"><span>EXAM</span></div>
  <div class="tile tile--services" role="img" aria-label="Eye care equipment"><span>SERVICES</span></div>
  <div class="tile tile--eyewear" role="img" aria-label="Woman trying on glasses"><span>EYEWEAR</span></div>
  <div class="tile tile--myopia" role="img" aria-label="Child wearing an eye patch"><span>MYOPIA CONTROL CLINIC</span></div>
</section>

<section class="testimonials">
  <svg class="chev" style="left:26px" width="16" height="28" viewBox="0 0 16 28"><path d="M14 2 2 14l12 12" fill="none" stroke="#fff" stroke-width="2"/></svg>
  <div class="testimonial-photo" role="img" aria-label="Young patient in front of an eye chart"></div>
  <h2 class="testimonial-title heading">Testimonials</h2>
  <p class="testimonial-quote"><span class="q">“</span> Lorem Ipsum is simply dummy text of the printing and typesetting industry. Lorem Ipsum has been the industry's standard dummy text ever since the 1500s, when an unknown printer. <span class="q">”</span></p>
  <div class="client-name">CLIENT NAME</div>
  <svg class="chev" style="left:1158px" width="16" height="28" viewBox="0 0 16 28"><path d="m2 2 12 12L2 26" fill="none" stroke="#fff" stroke-width="2"/></svg>
</section>

<section class="partners">
  <h2 class="partners-title heading">Our Partners</h2>
  <svg class="abs" style="left:78px;top:176px" width="14" height="26" viewBox="0 0 14 26"><path d="M12 2 2 13l10 11" fill="none" stroke="#aaa" stroke-width="2"/></svg>
  <div class="partner-row">
    <div class="partner-badge"></div><div class="partner-badge"></div><div class="partner-badge"></div><div class="partner-badge"></div><div class="partner-badge"></div>
  </div>
  <svg class="abs" style="left:1108px;top:176px" width="14" height="26" viewBox="0 0 14 26"><path d="m2 2 10 11L2 24" fill="none" stroke="#aaa" stroke-width="2"/></svg>
</section>

<section class="eyewear-section">
  <h2 class="eyewear-title heading">Select Eyewear</h2>
  <div class="product" style="left:86px">
    <div class="product-visual" role="img" aria-label="Black square sunglasses"><span class="cart"><svg width="18" height="16" viewBox="0 0 18 16"><path d="M1 1h3l2 9h9l2-6H5" fill="none" stroke="#222" stroke-width="1.8"/><circle cx="7" cy="14" r="1.5" fill="#222"/><circle cx="14" cy="14" r="1.5" fill="#222"/></svg></span></div>
    <div class="product-name">COMPNY NAME</div><div class="product-price">$22.00</div>
  </div>
  <div class="product" style="left:447px">
    <div class="product-visual" role="img" aria-label="Dark cat-eye sunglasses"><span class="cart"><svg width="18" height="16" viewBox="0 0 18 16"><path d="M1 1h3l2 9h9l2-6H5" fill="none" stroke="#222" stroke-width="1.8"/><circle cx="7" cy="14" r="1.5" fill="#222"/><circle cx="14" cy="14" r="1.5" fill="#222"/></svg></span></div>
    <div class="product-name">COMPNY NAME</div><div class="product-price">$22.00</div>
  </div>
  <div class="product" style="left:808px">
    <div class="product-visual" role="img" aria-label="Round black sunglasses"><span class="cart"><svg width="18" height="16" viewBox="0 0 18 16"><path d="M1 1h3l2 9h9l2-6H5" fill="none" stroke="#222" stroke-width="1.8"/><circle cx="7" cy="14" r="1.5" fill="#222"/><circle cx="14" cy="14" r="1.5" fill="#222"/></svg></span></div>
    <div class="product-name">COMPNY NAME</div><div class="product-price">$22.00</div>
  </div>
</section>

<footer class="site-footer">
  <div class="footer-brand"><div class="mark"></div><div class="name">LUMORA</div></div>
  <div class="cards-note">We Accepted Credit Card</div>
  <div class="social-row"><span></span><span></span><span></span></div>

  <div class="footer-col" style="left:343px">
    <h3>Lumora Optometry</h3>
    <ul>
      <li><svg width="16" height="20" viewBox="0 0 18 22"><path fill="#1a8fae" d="M9 0a8 8 0 0 0-8 8c0 6 8 14 8 14s8-8 8-14a8 8 0 0 0-8-8zm0 11a3 3 0 1 1 0-6 3 3 0 0 1 0 6z"/></svg><span>4820 Alderline Ave., Brookvale,<br>CA 90120</span></li>
      <li><svg width="16" height="16" viewBox="0 0 24 24"><path fill="#1a8fae" d="M6.6 10.8a15.1 15.1 0 0 0 6.6 6.6l2.2-2.2a1 1 0 0 1 1-.25 11.4 11.4 0 0 0 3.6.57 1 1 0 0 1 1 1V20a1 1 0 0 1-1 1A17 17 0 0 1 3 4a1 1 0 0 1 1-1h3.5a1 1 0 0 1 1 1c0 1.25.2 2.45.57 3.6a1 1 0 0 1-.25 1z"/></svg><span>555-204-7310</span></li>
      <li><svg width="16" height="16" viewBox="0 0 18 18"><rect x="4" y="1" width="10" height="5" fill="#1a8fae"/><rect x="1" y="7" width="16" height="8" rx="1" fill="#1a8fae"/><rect x="4" y="12" width="10" height="5" fill="#1a8fae"/></svg><span>555-204-7370</span></li>
      <li><svg width="16" height="13" viewBox="0 0 18 14"><rect width="18" height="14" rx="1" fill="#1a8fae"/><path d="m1 1 8 7 8-7" fill="none" stroke="#1e1e1e" stroke-width="1.6"/></svg><span>info@brivaloka.com</span></li>
    </ul>
    <span class="dir">Get Diraction</span>
  </div>

  <div class="footer-col" style="left:607px">
    <h3>Cedar Hollow</h3>
    <ul>
      <li><svg width="16" height="20" viewBox="0 0 18 22"><path fill="#1a8fae" d="M9 0a8 8 0 0 0-8 8c0 6 8 14 8 14s8-8 8-14a8 8 0 0 0-8-8zm0 11a3 3 0 1 1 0-6 3 3 0 0 1 0 6z"/></svg><span>2214 Fernmoor St.,<br>Suite 4, Cedar Hollow, CA<br>90145</span></li>
      <li><svg width="16" height="16" viewBox="0 0 24 24"><path fill="#1a8fae" d="M6.6 10.8a15.1 15.1 0 0 0 6.6 6.6l2.2-2.2a1 1 0 0 1 1-.25 11.4 11.4 0 0 0 3.6.57 1 1 0 0 1 1 1V20a1 1 0 0 1-1 1A17 17 0 0 1 3 4a1 1 0 0 1 1-1h3.5a1 1 0 0 1 1 1c0 1.25.2 2.45.57 3.6a1 1 0 0 1-.25 1z"/></svg><span>555-318-6620</span></li>
      <li><svg width="16" height="13" viewBox="0 0 18 14"><rect width="18" height="14" rx="1" fill="#1a8fae"/><path d="m1 1 8 7 8-7" fill="none" stroke="#1e1e1e" stroke-width="1.6"/></svg><span>cedarhollow@brivaloka.com</span></li>
    </ul>
    <span class="dir">Get Diraction</span>
  </div>

  <div class="footer-col newsletter" style="left:874px">
    <h3>Newsletter</h3>
    <p>Would you like to Recieve our exclusive update for sign up our newsletter !</p>
    <div class="news-input">Enter Email</div>
    <div class="news-btn">SUBSCRIBE</div>
  </div>

  <div class="footer-badges"><span class="b1"></span><span class="b2"></span></div>
</footer>
<div class="copyright">©2019 <b>Lumora Optometry</b> - All Right Reserved.</div>

</body>
</html>
```